One of a kind service business!

We are the only ocean freight auditing company in the entire world that does what we do. We provide a innovative service in auditing our clients invoices for billing errors as it relates to the import and export of their products anywhere in the world. We'd like to retain the current logo - but we are open to any interesting concepts that can complete the card.

Target Market(s)

C-Level and Senior Financial executives

Industry/Entity Type

Auditing

Requirements
Must have

• ONE SIDED ONLY
Should not have
• no cartoonish images

```html
<!DOCTYPE html>
<html lang="en">
<head>
<meta charset="utf-8">
<title>Tidemark Review – Business Card</title>
<link rel="stylesheet" href="https://fonts.googleapis.com/css2?family=Comfortaa:wght@400;700&display=swap">
<style>
  :root {
    --backdrop: #e7ebe8;
    --card: #6d3946;
    --text-main: #f4eef0;
    --text-soft: #c7aeb5;
    --text-muted: #b3959d;
    --brand: #8fd0ec;
  }
  * { margin: 0; padding: 0; box-sizing: border-box; }
  html, body {
    width: 1200px;
    height: 898px;
    overflow: hidden;
    background: var(--backdrop);
    font-family: "Comfortaa", sans-serif;
  }
  .canvas {
    position: relative;
    width: 1200px;
    height: 898px;
  }
  .business-card {
    position: absolute;
    left: 460px;
    top: 178px;
    width: 356px;
    height: 582px;
    background: var(--card);
    color: var(--text-main);
  }
  .holder {
    position: absolute;
    left: 38px;
    top: 34px;
  }
  .holder-name {
    font-weight: 700;
    font-size: 19px;
    letter-spacing: 0.3px;
  }
  .holder-title {
    margin-top: 6px;
    font-size: 13px;
    color: var(--text-soft);
  }
  .brand-name {
    position: absolute;
    left: 38px;
    top: 290px;
    font-weight: 700;
    font-size: 24px;
    color: var(--brand);
    letter-spacing: 0.5px;
  }
  .contact {
    position: absolute;
    left: 38px;
    top: 392px;
    list-style: none;
    font-size: 12.5px;
    line-height: 18px;
    color: var(--text-soft);
  }
  .contact .label {
    display: inline-block;
    min-width: 14px;
    font-weight: 700;
    color: var(--text-main);
  }
  .tagline {
    position: absolute;
    left: 318px;
    top: 512px;
    transform: rotate(-90deg);
    transform-origin: left top;
    white-space: nowrap;
    font-size: 12px;
    letter-spacing: 2.6px;
    text-transform: uppercase;
    color: var(--text-muted);
  }
</style>
</head>
<body>
<main class="canvas">
  <article class="business-card">
    <header class="holder">
      <h1 class="holder-name">Martin Keller</h1>
      <p class="holder-title">CEO</p>
    </header>

    <p class="brand-name">Tidemark Review</p>

    <ul class="contact">
      <li>Harbor Point Center, Lodni 12</li>
      <li>Portview – Czech Republic 120 00</li>
      <li><span class="label">p</span> +420 200 555 014</li>
      <li><span class="label">m</span> +420 600 555 027</li>
      <li><span class="label">USA</span> +1 555 010 7742</li>
      <li><span class="label">f</span> +420 200 555 090</li>
      <li><span class="label">e</span> martin.k@tidemarkreview.net</li>
      <li><span class="label">w</span> www.tidemarkreview.net</li>
    </ul>

    <p class="tagline">Get a free estimate of your refund today</p>
  </article>
</main>
</body>
</html>
```